Venture 482 - Lumora Book Cover

I am looking for a Lumora book cover for my book about "Venture 482".
The Book is Titled:
Venture 482 Ascended
Shaping Outcomes: Paths To Unlocking Cosmic Truths
Author is Dorian Pell
Here is a book description that may help you understand more about it:
Inspired by the genius of Edwin Marlowe, this comprehensive guide delves into the ancient wisdom and cutting-edge science behind the 482 method, a powerful tool for manifesting your desires. Whether you're seeking personal growth, financial success, or spiritual enlightenment, this book provides advanced techniques and methods to transform your dreams into reality.
Any questions please ask.
Thanks
Owen

```html
<!DOCTYPE html>
<html lang="en">
<head>
<meta charset="utf-8">
<title>Venture 482 Ascended — Dorian Pell</title>
<link rel="stylesheet" href="https://fonts.googleapis.com/css2?family=Cinzel:wght@400;500&family=Crimson+Text:wght@400;600&display=swap">
<style>
  :root {
    --ink-black: #050505;
    --blush: #f2d8cd;
    --cream: #fcefe6;
    --white: #ffffff;
    --ring-gold: #d9a92a;
    --ring-blue: #2c8fd6;
    --ring-green: #5fae3b;
    --ring-violet: #8a3fc0;
    --ring-red: #d23a3a;
  }
  * { margin: 0; padding: 0; box-sizing: border-box; }
  html, body { width: 805px; height: 1200px; overflow: hidden; background: var(--ink-black); }
  .cover {
    position: relative;
    width: 805px;
    height: 1200px;
    background: var(--ink-black);
    overflow: hidden;
  }
  .cover-art { position: absolute; inset: 0; width: 805px; height: 1200px; }
  .author, .title-word, .title-number, .title-edition, .subtitle-lead, .subtitle-body {
    position: absolute;
    left: 0;
    width: 100%;
    text-align: center;
    line-height: 1;
  }
  .author {
    top: 48px;
    font-family: "Cinzel", serif;
    font-weight: 400;
    font-size: 43px;
    letter-spacing: 0.32em;
    padding-left: 0.32em;
    color: var(--blush);
  }
  .title-word {
    top: 402px;
    font-family: "Cinzel", serif;
    font-weight: 400;
    font-size: 98px;
    letter-spacing: 0.01em;
    color: var(--cream);
  }
  .title-number {
    top: 522px;
    font-family: "Cinzel", serif;
    font-weight: 400;
    font-size: 340px;
    letter-spacing: -0.06em;
    color: var(--cream);
  }
  .title-edition {
    top: 833px;
    font-family: "Cinzel", serif;
    font-weight: 400;
    font-size: 42px;
    letter-spacing: 0.62em;
    padding-left: 0.62em;
    color: var(--cream);
  }
  .subtitle-lead {
    top: 912px;
    font-family: "Crimson Text", serif;
    font-weight: 400;
    font-size: 30px;
    color: var(--white);
  }
  .subtitle-body {
    top: 966px;
    font-family: "Crimson Text", serif;
    font-weight: 400;
    font-size: 27px;
    line-height: 35px;
    color: var(--white);
  }
</style>
</head>
<body>
<main class="cover">
  <svg class="cover-art" viewBox="0 0 805 1200" xmlns="http://www.w3.org/2000/svg">
    <defs>
      <radialGradient id="figure-glow" cx="50%" cy="50%" r="50%">
        <stop offset="0%" stop-color="#2a3a3a"/>
        <stop offset="45%" stop-color="#1a2020"/>
        <stop offset="100%" stop-color="#070707"/>
      </radialGradient>
      <linearGradient id="ring-spectrum" x1="0" y1="0" x2="1" y2="1">
        <stop offset="0%" stop-color="var(--ring-green)"/>
        <stop offset="25%" stop-color="var(--ring-blue)"/>
        <stop offset="50%" stop-color="var(--ring-violet)"/>
        <stop offset="75%" stop-color="var(--ring-blue)"/>
        <stop offset="100%" stop-color="var(--ring-gold)"/>
      </linearGradient>
      <linearGradient id="ring-spectrum-inner" x1="1" y1="0" x2="0" y2="1">
        <stop offset="0%" stop-color="var(--ring-red)"/>
        <stop offset="35%" stop-color="var(--ring-gold)"/>
        <stop offset="70%" stop-color="var(--ring-gold)"/>
        <stop offset="100%" stop-color="var(--ring-blue)"/>
      </linearGradient>
      <radialGradient id="floor-glow" cx="50%" cy="50%" r="50%">
        <stop offset="0%" stop-color="#e8d24a" stop-opacity="0.9"/>
        <stop offset="40%" stop-color="#3fae6a" stop-opacity="0.6"/>
        <stop offset="75%" stop-color="#c8404a" stop-opacity="0.3"/>
        <stop offset="100%" stop-color="#050505" stop-opacity="0"/>
      </radialGradient>
    </defs>

    <g class="cosmic-figure" role="img" aria-label="Illustration of a standing human figure with arms outstretched, drawn with coloured veins and nerves, surrounded by stars, planets and scientific sketches">
      <circle cx="402" cy="570" r="372" fill="url(#figure-glow)"/>
      <ellipse cx="402" cy="1112" rx="300" ry="26" fill="url(#floor-glow)"/>
    </g>

    <g class="orbit-rings" fill="none">
      <circle cx="402" cy="570" r="396" stroke="url(#ring-spectrum)" stroke-width="4"/>
      <circle cx="402" cy="570" r="380" stroke="url(#ring-spectrum-inner)" stroke-width="3"/>
      <circle cx="402" cy="570" r="356" stroke="var(--ring-gold)" stroke-width="1.5" opacity="0.7"/>
      <line x1="402" y1="80" x2="402" y2="1120" stroke="var(--ring-gold)" stroke-width="1.5" opacity="0.8"/>
    </g>
  </svg>

  <p class="author">DORIAN PELL</p>
  <h1>
    <span class="title-word">VENTURE</span>
    <span class="title-number">482</span>
    <span class="title-edition">ASCENDED</span>
  </h1>
  <p class="subtitle-lead">SHAPING OUTCOMES:</p>
  <p class="subtitle-body">Paths to unlocking<br>cosmic truths</p>
</main>
</body>
</html>
```